Thornvale Group needs a business card design

We need a new business card design using the logo recently selected in a logo competition on Pixel Bazaar. Our business is a consultancy specializing in aviation and energy and the winning business card design will promote an image of precision and professionalism with creativity.

Please use the logo with the name on the front of the card and use a complementary font. Make the back white with either the light grey or dark grey logo.

Target Market(s)

Senior finance and legal leaders at aviation and energy companies

Industry/Entity Type

Management Consulting

Contact Information for Business Card

Peter Castrell
President
Thornvale Group

www.thornvalegroup.example

(555) 204-6391
pc@thornvalegroup.example

Requirements
Must have
• Professional font that goes well with the logo font

```html
<!DOCTYPE html>
<html lang="en">
<head>
<meta charset="utf-8">
<title>Thornvale Group – Business Card</title>
<link rel="stylesheet" href="https://fonts.googleapis.com/css2?family=Arimo:wght@400;700&display=swap">
<style>
  :root {
    --navy: #0f4174;
    --navy-deep: #0b3763;
    --paper: #ffffff;
    --paper-shade: #e9eaec;
    --logo-grey: #6b7077;
    --ink-grey: #555a60;
    --backdrop: #ecebe8;
    --text-light: #ffffff;
  }
  * { box-sizing: border-box; margin: 0; padding: 0; }
  html, body {
    width: 1200px; height: 950px; overflow: hidden;
    background: var(--backdrop);
    font-family: "Arimo", Arial, sans-serif;
  }
  .sheet {
    width: 1200px; height: 950px;
    display: flex; flex-direction: column; align-items: center; justify-content: center;
    gap: 40px;
  }
  .card {
    width: 735px; height: 420px;
    box-shadow: 0 6px 18px rgba(0,0,0,.18);
    position: relative; overflow: hidden;
  }
  /* Front */
  .card-front { display: flex; background: var(--paper); }
  .contact-panel {
    width: 52%; height: 100%;
    background: linear-gradient(180deg, var(--navy) 0%, var(--navy-deep) 100%);
    color: var(--text-light);
    padding: 46px 34px 0 44px;
  }
  .holder-name { font-size: 25px; font-weight: 700; }
  .holder-title { font-size: 17px; font-weight: 400; margin-top: 4px; }
  .divider {
    border: none; border-top: 2px dotted rgba(255,255,255,.85);
    margin: 24px 0 20px;
  }
  .company-lines p { font-size: 17px; line-height: 1.32; }
  .contact-list { list-style: none; }
  .contact-list li {
    display: flex; align-items: center; gap: 10px;
    font-size: 17px; line-height: 1.35;
  }
  .contact-list svg { width: 15px; height: 15px; flex: none; }
  .brand-panel {
    flex: 1; display: flex; align-items: center; justify-content: center;
    background: linear-gradient(135deg, var(--paper) 0%, var(--paper-shade) 100%);
  }
  .brand-name {
    font-size: 32px; font-weight: 400;
    letter-spacing: 0; text-align: center; white-space: nowrap;
  }
  .card-front .brand-name { color: var(--navy); margin-top: 60px; }
  /* Back */
  .card-back {
    background: linear-gradient(135deg, var(--paper) 0%, var(--paper-shade) 100%);
    display: flex; flex-direction: column; align-items: center; justify-content: center;
    gap: 22px;
  }
  .card-back .brand-name { color: var(--logo-grey); font-size: 38px; }
  .back-web { color: var(--ink-grey); font-size: 17px; letter-spacing: 2px; }
</style>
</head>
<body>
<main class="sheet">
  <section class="card card-front">
    <div class="contact-panel">
      <h1 class="holder-name">Peter J. Castrell</h1>
      <p class="holder-title">President</p>
      <hr class="divider">
      <div class="company-lines">
        <p>Thornvale Group LLC</p>
        <p>Finance and Strategy Consulting</p>
        <p>Aviation - Manufacturing - Energy</p>
      </div>
      <hr class="divider">
      <ul class="contact-list">
        <li>
          <svg viewBox="0 0 16 16" aria-hidden="true"><path fill="#fff" d="M3 2h3l1 3-2 1c1 2 3 4 5 5l1-2 3 1v3c0 1-1 1-1 1C7 14 2 9 2 3c0 0 0-1 1-1z"/></svg>
          <span>(555) 204-6391</span>
        </li>
        <li>
          <svg viewBox="0 0 16 16" aria-hidden="true"><rect x="1" y="3" width="14" height="10" fill="#fff"/><path d="M1 3l7 6 7-6" fill="none" stroke="#0f4174" stroke-width="1.4"/></svg>
          <span>pc@thornvalegroup.example</span>
        </li>
        <li>
          <svg viewBox="0 0 16 16" aria-hidden="true"><circle cx="8" cy="8" r="7" fill="#fff"/><path d="M1 8h14M8 1c-3 4-3 10 0 14M8 1c3 4 3 10 0 14" fill="none" stroke="#0f4174" stroke-width="1.1"/></svg>
          <span>thornvalegroup.example</span>
        </li>
      </ul>
    </div>
    <div class="brand-panel">
      <p class="brand-name">Thornvale Group</p>
    </div>
  </section>

  <section class="card card-back">
    <p class="brand-name">Thornvale Group</p>
    <p class="back-web">www.thornvalegroup.example</p>
  </section>
</main>
</body>
</html>
```